Web design required

1-We need a web design for existing company based in New Zealand
2-We build residential house and light commercial
3-We has in-house designer which allow us can provide interior design
4-We modeling project before site construction, which enable both client and construction team to visually analysis whole project,

Target Market(s)

middle class residential house market
Ref: http://www.parvellbuilders.co.nz/

Industry/Entity Type

Construction Company

Number of Pages Required

1 page

Font styles to use
Sans Serif
Other font styles liked:
• Such as : Central Gothic or similar which has more design taste

Colors

Designer to choose colors to be used in the design.

Requirements
Must have
• Front sheet, contact information, sample project

```html
<!DOCTYPE html>
<html lang="en">
<head>
<meta charset="utf-8">
<title>Kestrel Homes</title>
<link rel="stylesheet" href="https://fonts.googleapis.com/css2?family=Montserrat:wght@400;500;600;700&family=Open+Sans:wght@400;600&display=swap">
<style>
:root{
  --blue:#0c4f9e;
  --ink:#2e2e2e;
  --text:#555;
  --muted:#8a8a8a;
  --grey:#efefef;
  --white:#fff;
  --line:#e2e2e2;
}
*{box-sizing:border-box;margin:0;padding:0}
html,body{width:1200px;height:3509px;overflow:hidden}
body{position:relative;background:var(--white);font-family:"Open Sans",Arial,sans-serif;color:var(--text)}
.abs{position:absolute}
.hex{clip-path:polygon(50% 0,100% 25%,100% 75%,50% 100%,0 75%,0 25%)}
.brand{display:flex;align-items:center;gap:12px;font-family:"Montserrat",Arial,sans-serif;font-weight:600;color:var(--ink);letter-spacing:.5px;white-space:nowrap}
.brand-mark{width:40px;height:40px;background:var(--blue)}

/* header */
.site-header{left:0;top:0;width:1200px;height:100px;background:var(--white);z-index:3}
.site-header .brand{position:absolute;left:75px;top:30px;font-size:28px}
.main-nav{position:absolute;left:440px;top:48px;display:flex;gap:42px;font-family:"Montserrat",Arial,sans-serif;font-size:14px;color:var(--ink);text-transform:uppercase}
.main-nav .active{color:var(--blue);font-weight:600}
.quote{position:absolute;left:970px;top:30px;font-family:"Montserrat",Arial,sans-serif}
.quote small{display:block;color:var(--blue);font-size:13px;font-weight:700}
.quote strong{display:block;font-size:28px;color:var(--ink);font-weight:600;letter-spacing:1px}

/* hero */
.hero{left:0;top:100px;width:1200px;height:545px;background:linear-gradient(180deg,#5c82b8 0%,#8fa9c9 40%,#6f6c63 70%,#4a6a38 100%)}
.hero-text{left:0;top:300px;width:1200px;text-align:center;color:var(--white);font-family:"Montserrat",Arial,sans-serif}
.hero-text h1{font-size:50px;font-weight:600;letter-spacing:1px}
.hero-text p{font-size:28px;font-weight:600;line-height:36px;margin-top:2px}
.dots{left:567px;top:482px;display:flex;gap:10px}
.dots i{width:10px;height:10px;border-radius:50%;background:var(--white)}
.dots i.on{background:var(--blue)}

/* about */
.band-grey{left:0;top:1168px;width:1200px;height:700px;background:var(--grey)}
.about-hex{left:636px;top:538px;width:608px;height:737px;background:var(--white);z-index:2}
.about-photo{left:656px;top:562px;width:580px;height:690px;background:linear-gradient(180deg,#8eb2dc 0%,#b9c9d8 35%,#6f7276 65%,#5c5a52 100%);z-index:2}
h2{font-family:"Montserrat",Arial,sans-serif;font-weight:700;font-size:42px;color:var(--ink);letter-spacing:1px}
.about-title{left:75px;top:750px}
.about .brand{position:absolute;left:75px;top:800px;font-size:28px}
.about-copy{left:75px;top:875px;width:520px;font-size:15px;line-height:26px}
.about-copy p+p{margin-top:10px}
.btn{display:flex;align-items:center;justify-content:center;background:var(--blue);color:var(--white);font-family:"Montserrat",Arial,sans-serif;font-weight:700;font-size:13px;text-transform:uppercase;letter-spacing:.5px}
.about-btn{left:75px;top:1065px;width:166px;height:55px}

/* services */
.services-title{left:75px;top:1220px}
.service{width:292px;height:340px;display:flex;align-items:center;justify-content:center;text-align:center;color:var(--white);font-family:"Montserrat",Arial,sans-serif;font-weight:700;font-size:28px;line-height:33px}
.s1{left:95px;top:1312px;background:linear-gradient(135deg,#d9cfcf,#a9a2a6 60%,#c55b7c)}
.s2{left:455px;top:1312px;background:linear-gradient(160deg,#8c8a86,#6d6458 50%,#b7b0a7)}
.s3{left:814px;top:1312px;background:linear-gradient(170deg,#c9a679,#7a6a58 55%,#5a5a5a)}
.fold{left:0;top:1690px}

/* projects */
.projects-title{left:0;top:1880px;width:1200px;text-align:center}
.project{width:286px;height:328px;display:flex;align-items:center;justify-content:center;color:var(--white);font-family:"Montserrat",Arial,sans-serif;font-weight:600;font-size:22px}
.p1{left:164px;top:1966px;background:linear-gradient(180deg,#6e7f96,#4f5a66 60%,#3c4148)}
.p2{left:456px;top:1966px;background:linear-gradient(180deg,#6f7884,#8e8f8e 55%,#4c4d4f)}
.p3{left:749px;top:1966px;background:linear-gradient(180deg,#3d3f42,#2f3033 50%,#6e5a3d)}
.p4{left:311px;top:2223px;background:linear-gradient(180deg,#545a60,#3f4246 55%,#25272a)}
.p5{left:603px;top:2223px;background:linear-gradient(180deg,#9eb5d8,#5b6f8a 50%,#3a3f48)}
.projects-btn{left:496px;top:2593px;width:208px;height:54px}

/* contact */
.band-contact{left:0;top:2720px;width:1200px;height:686px;background:var(--grey)}
.notch{left:0;top:2719px}
.contact-title{left:75px;top:2770px}
.label{font-family:"Montserrat",Arial,sans-serif;font-weight:700;font-size:15px;color:var(--blue);text-transform:uppercase;letter-spacing:.5px}
.office{left:75px;top:2848px;font-size:15px}
.office .addr{margin-top:8px}
.office .lines{margin-top:12px;display:flex;gap:26px;color:var(--blue);font-weight:600;align-items:center}
.office .lines span{display:flex;align-items:center;gap:12px}
.map{left:75px;top:2946px;width:512px;height:279px;background:linear-gradient(135deg,#e6e4df,#d8dde0 50%,#cfe3c8);border:4px solid var(--white)}
.inquiry{left:655px;top:2848px;width:470px}
.inquiry p{font-size:15px;line-height:24px;margin-top:6px}
.field{background:var(--white);font-size:13px;color:var(--text);padding:15px 14px}
.f-name{left:655px;top:2948px;width:230px;height:47px}
.f-phone{left:896px;top:2948px;width:229px;height:47px}
.f-email{left:655px;top:3005px;width:470px;height:46px}
.f-msg{left:655px;top:3058px;width:470px;height:102px}
.send-btn{left:962px;top:3171px;width:163px;height:54px}
.follow{left:655px;top:3266px}
.socials{left:655px;top:3302px;display:flex;gap:20px}
.socials i{width:22px;height:22px;border-radius:50%;background:#6b6b6b}

/* footer */
.foot-hex{left:100px;top:3265px;width:326px;height:300px;background:var(--white)}
.footer-bar{left:0;top:3406px;width:1200px;height:103px;background:var(--white)}
.foot-brand{left:0;top:3300px;width:526px;display:flex;flex-direction:column;align-items:center;gap:14px;font-family:"Montserrat",Arial,sans-serif;font-weight:600;font-size:28px;color:var(--ink)}
.foot-brand .brand-mark{width:50px;height:50px}
.copyright{left:0;top:3438px;width:526px;text-align:center;font-size:12px;line-height:18px;color:var(--text)}
.foot-nav{left:660px;top:3450px;display:flex;gap:36px;font-family:"Montserrat",Arial,sans-serif;font-size:13px;color:var(--ink);text-transform:uppercase}
</style>
</head>
<body>

<header class="abs site-header">
  <div class="brand"><span class="brand-mark"></span>KESTREL HOMES</div>
  <nav class="main-nav">
    <span class="active">Home</span><span>About Us</span><span>Services</span><span>Projects</span><span>Contact Us</span>
  </nav>
  <div class="quote"><small>GET A QUOTE:</small><strong>09 480 3172</strong></div>
</header>

<section class="abs hero" role="img" aria-label="Modern two-storey home with white render and timber cladding under a blue sky"></section>
<div class="abs hero-text">
  <h1>Welcome to Kestrel Homes</h1>
  <p>We build residential house and<br>light commercial.</p>
</div>
<div class="abs dots"><i class="on"></i><i></i><i></i><i></i></div>

<div class="abs band-grey"></div>

<section class="about">
  <div class="abs hex about-hex"></div>
  <div class="abs hex about-photo" role="img" aria-label="House under construction wrapped in scaffolding"></div>
  <h2 class="abs about-title">ABOUT</h2>
  <div class="brand"><span class="brand-mark"></span>KESTREL HOMES</div>
  <div class="abs about-copy">
    <p>Kestrel Homes is dedicated to creating and renovating beautiful and unusual buildings.</p>
    <p>Kestrel Homes works with you to take dream houses off the blueprints and into reality. We have the knowledge and expertise to customise homes to suit you – from unusual materials and designs to environmentally sensitive locations.</p>
  </div>
  <div class="abs btn about-btn">Read More</div>
</section>

<section class="services">
  <h2 class="abs services-title">OUR SERVICES</h2>
  <div class="abs hex service s1" role="img" aria-label="Hands sketching plans on paper">Preconstruction<br>Planning</div>
  <div class="abs hex service s2" role="img" aria-label="Scale house model on drawings">Construction<br>Modelling</div>
  <div class="abs hex service s3" role="img" aria-label="Site team in hard hats inside a timber frame">Full Project<br>Management</div>
  <svg class="abs fold" width="1200" height="180" viewBox="0 0 1200 180" aria-hidden="true">
    <polygon points="0,178 0,150 270,8 560,180" fill="#fff"/>
    <polygon points="0,180 1200,180 1200,170 0,170" fill="#fff"/>
  </svg>
</section>

<section class="projects">
  <h2 class="abs projects-title">OUR PROJECTS</h2>
  <div class="abs hex project p1" role="img" aria-label="Multi-unit apartment block">Ashford Project</div>
  <div class="abs hex project p2" role="img" aria-label="Weatherboard townhouses">Belmont Project</div>
  <div class="abs hex project p3" role="img" aria-label="Dark clad home with balcony">Coralbay Project</div>
  <div class="abs hex project p4" role="img" aria-label="Contemporary dark home at dusk">Dunmore Project</div>
  <div class="abs hex project p5" role="img" aria-label="Lit gable-roof home at twilight">Elm Rd Project</div>
  <div class="abs btn projects-btn">View All Projects</div>
</section>

<div class="abs band-contact"></div>
<svg class="abs notch" width="1200" height="110" viewBox="0 0 1200 110" aria-hidden="true">
  <polygon points="400,0 936,104 1200,20 1200,0" fill="#fff"/>
</svg>

<section class="contact">
  <h2 class="abs contact-title">CONTACT US</h2>
  <div class="abs office">
    <div class="label">Head Office</div>
    <div class="addr">27 Harbourview Lane, Eastfield Auckland</div>
    <div class="lines">
      <span><svg width="14" height="14" viewBox="0 0 24 24"><path fill="#0c4f9e" d="M6.6 10.8a15 15 0 0 0 6.6 6.6l2.2-2.2c.3-.3.7-.4 1-.2 1.1.4 2.3.6 3.6.6.6 0 1 .4 1 1V20c0 .6-.4 1-1 1A17 17 0 0 1 3 4c0-.6.4-1 1-1h3.5c.6 0 1 .4 1 1 0 1.3.2 2.5.6 3.6.1.3 0 .7-.2 1z"/></svg>0064 9 480 3172</span>
      <span><svg width="16" height="12" viewBox="0 0 16 12"><rect width="16" height="12" fill="#0c4f9e"/><path d="M0 0l8 6 8-6" stroke="#fff" stroke-width="1.4" fill="none"/></svg>hello@kestrelhomes.co.nz</span>
    </div>
  </div>
  <div class="abs map" role="img" aria-label="Street map showing the head office location"></div>

  <div class="abs inquiry">
    <div class="label">Inquiries</div>
    <p>For any inquiries, questions or commendations, please call or fill out the following form...</p>
  </div>
  <div class="abs field f-name">Name</div>
  <div class="abs field f-phone">Phone No.</div>
  <div class="abs field f-email">Email Address</div>
  <div class="abs field f-msg">Message</div>
  <div class="abs btn send-btn">Read More</div>

  <div class="abs label follow">Follow Us</div>
  <div class="abs socials"><i></i><i></i><i></i><i></i><i></i></div>
</section>

<div class="abs hex foot-hex"></div>
<footer>
  <div class="abs footer-bar"></div>
  <div class="abs foot-brand"><span class="brand-mark"></span>KESTREL HOMES</div>
  <div class="abs copyright">Copyright © 2017 by Kestrel Homes<br>All Right Reserved</div>
  <nav class="abs foot-nav"><span>Home</span><span>About Us</span><span>Services</span><span>Projects</span><span>Contact Us</span></nav>
</footer>

</body>
</html>
```